Construction material supplies company business card ****

1. Full company name “K T Masonry Works Ltd”
I am after a Business card design for the company as a whole. We are better known in Solomon Islands as “K T Masonry” for short.

We are a building materials supplier of
Ready Mixed Concrete, Bricks and Blocks,
Quarry products- gravel, aggregates, sand etc.
Cement distributor/retailer of reputable brands.
Other prefab concrete products. Culverts, wave breakers, concrete retaining blocks etc.

2. Competitive Advantage over Competition: Quality, efficient, professional, dependable, reliable

3. We want people to feel trust worthy, high quality, strong when they see our brand

5. No preference to color. Maybe more sturdy and corporate. Not fancy.

Industry/Entity Type

CONSTRUCTION SUPPLY

Contact Information for Business Card

Name, Position, office phone mob phone, email

Requirements
Must have
• the company logo
Nice to have
• would like to see a mixture of designs, of with logo only and also with simple graphic designs to bring out the company whilst still have the strong sturdy professional feeling

```html
<!DOCTYPE html>
<html lang="en">
<head>
<meta charset="utf-8">
<title>K T Masonry – Business Card</title>
<link href="https://fonts.googleapis.com/css2?family=Arimo:wght@400;700&display=swap" rel="stylesheet">
<style>
  :root {
    --navy: #154168;
    --white: #ffffff;
    --backdrop: #2a2a2a;
  }
  html, body {
    margin: 0;
    padding: 0;
    width: 1200px;
    height: 1015px;
    overflow: hidden;
    background: var(--backdrop);
    font-family: "Arimo", Arial, sans-serif;
  }
  .sheet {
    width: 1200px;
    height: 1015px;
    display: flex;
    flex-direction: column;
    align-items: center;
    justify-content: center;
    gap: 45px;
  }
  .card {
    position: relative;
    width: 700px;
    height: 400px;
    overflow: hidden;
    box-shadow: 0 14px 30px rgba(0,0,0,.55);
  }
  .card-front {
    background: var(--navy);
    display: flex;
    align-items: center;
    justify-content: center;
  }
  .brand {
    display: flex;
    align-items: center;
    gap: 18px;
    font-weight: 700;
    text-transform: uppercase;
    letter-spacing: 3px;
  }
  .brand-mark {
    width: 40px;
    height: 40px;
    border: 6px solid currentColor;
    box-sizing: border-box;
  }
  .card-front .brand { color: var(--white); font-size: 50px; }
  .card-back { background: var(--navy); }
  .card-back .art {
    position: absolute;
    inset: 0;
  }
  .card-back .brand {
    position: absolute;
    left: 385px;
    top: 118px;
    width: 290px;
    justify-content: center;
    color: var(--navy);
    font-size: 30px;
    gap: 12px;
    letter-spacing: 2px;
  }
  .card-back .brand-mark { width: 26px; height: 26px; border-width: 4px; }
  .person {
    position: absolute;
    left: 58px;
    top: 212px;
    color: var(--white);
  }
  .person-name {
    margin: 0;
    font-size: 24px;
    font-weight: 700;
    text-transform: uppercase;
    letter-spacing: .5px;
  }
  .person-title {
    margin: 2px 0 0;
    font-size: 17px;
  }
  .contacts {
    list-style: none;
    margin: 28px 0 0;
    padding: 0;
    font-size: 16px;
    line-height: 24px;
  }
  .contacts li { display: flex; align-items: center; gap: 10px; }
  .contacts svg { width: 16px; height: 16px; flex: none; }
</style>
</head>
<body>
<main class="sheet">
  <section class="card card-front" aria-label="Card front">
    <div class="brand"><span class="brand-mark"></span><span>K T Masonry</span></div>
  </section>

  <section class="card card-back" aria-label="Card back">
    <svg class="art" viewBox="0 0 700 400" aria-hidden="true">
      <circle cx="520" cy="120" r="255" fill="var(--white)"/>
      <circle cx="528" cy="112" r="244" fill="var(--navy)"/>
      <circle cx="532" cy="108" r="238" fill="var(--white)"/>
    </svg>
    <div class="brand"><span class="brand-mark"></span><span>K T Masonry</span></div>

    <div class="person">
      <h1 class="person-name">Daniel Harper</h1>
      <p class="person-title">Managing Director</p>
      <ul class="contacts">
        <li>
          <svg viewBox="0 0 16 16"><path d="M3 1.5l3 3-1.6 1.8c.9 2 2.3 3.4 4.3 4.3L10.5 9l3 3-2 2C6 13.5 2.5 10 2 4z" fill="var(--white)"/></svg>
          044-987 650 321
        </li>
        <li>
          <svg viewBox="0 0 16 16"><rect x="4" y="1.5" width="8" height="13" rx="1.5" fill="none" stroke="var(--white)" stroke-width="1.6"/></svg>
          044-987 650 321
        </li>
        <li>
          <svg viewBox="0 0 16 16"><rect x="1" y="3.5" width="14" height="9" fill="var(--white)"/><path d="M1 3.5l7 5 7-5" fill="none" stroke="var(--navy)" stroke-width="1.2"/></svg>
          info@ktmasonry.sb
        </li>
      </ul>
    </div>
  </section>
</main>
</body>
</html>
```